Quill Petal Loft Hair Salon needs a Webpage design

Quill Petal Loft in Englewood is looking to start their web page, url and business emails, we want to be able to upload pictures and videos on the website. we do blow outs , makeup, color, lash extension, gel manicures

Target Market(s)

everyone

Industry/Entity Type

Beauty Salon

Coding

Coded - Design and coding required

Number of Pages Required

5+ page

Font styles to use
Serif

Colors
ffcf3e
9d9d9d
000000
ffffff

Requirements
Must have
• about us, contact us, products, menu, location, gallery, press
Nice to have
• play video gallery

```html
<!DOCTYPE html>
<html lang="en">
<head>
<meta charset="utf-8">
<title>Quill Petal Loft Hair Salon</title>
<link rel="stylesheet" href="https://fonts.googleapis.com/css2?family=Raleway:wght@400;500;600&family=Open+Sans:wght@400;600&family=Playfair+Display:wght@400&display=swap">
<style>
:root{
  --gold:#ffcf3e;
  --gold-deep:#f5b800;
  --grey:#9d9d9d;
  --ink:#000000;
  --paper:#ffffff;
  --text:#333333;
  --muted:#8a8a8a;
  --band:#e8e8e8;
  --foot-bar:#333333;
}
*{margin:0;padding:0;box-sizing:border-box}
html,body{width:1200px;height:2624px;overflow:hidden;background:var(--paper)}
body{position:relative;font-family:"Open Sans",sans-serif;color:var(--text)}
.abs{position:absolute}

/* header */
.brand{left:143px;top:20px;display:flex;align-items:center;gap:12px}
.brand-dot{width:22px;height:22px;border-radius:50%;background:var(--gold)}
.brand-name{font-family:"Playfair Display",serif;font-size:34px;color:var(--gold-deep);line-height:1}
.phone{right:143px;top:44px;text-align:right}
.phone-label{font-size:16px;color:#666;margin-bottom:4px}
.phone-line{display:flex;align-items:center;gap:10px;font-size:24px;color:#222;font-family:"Raleway",sans-serif;font-weight:500}
.phone-icon{width:30px;height:30px;border-radius:50%;background:var(--gold-deep);display:flex;align-items:center;justify-content:center}

/* nav */
.nav{left:0;top:110px;width:1200px;height:51px;background:linear-gradient(var(--gold),var(--gold-deep))}
.nav ul{list-style:none;position:absolute;left:143px;top:0;display:flex;height:51px}
.nav li{height:51px;padding:0 28px;display:flex;align-items:center;color:var(--paper);font-family:"Raleway",sans-serif;font-size:17px;border-right:1px solid rgba(255,255,255,.45)}
.nav li.active{background:#2a1f0a;padding:0 38px}

/* hero */
.hero{left:0;top:161px;width:1200px;height:509px;background:linear-gradient(90deg,#f1f1f1 0%,#e2e2e2 40%,#bdbdbd 60%,#555 80%,#2e2e2e 100%)}
.hero-curve{left:0;top:560px}
.hero-kicker{left:143px;top:307px;font-family:"Raleway",sans-serif;font-size:30px;color:#111;font-weight:500}
.hero-title{left:143px;top:352px;font-family:"Raleway",sans-serif;font-size:40px;color:#111;font-weight:500}
.hero-text{left:149px;top:412px;width:390px;font-size:14px;line-height:21px;color:#444}
.btn-gold{background:linear-gradient(var(--gold),var(--gold-deep));color:var(--paper);font-family:"Raleway",sans-serif;display:flex;align-items:center;justify-content:center}
.hero-btn{left:149px;top:463px;width:136px;height:39px;font-size:15px}
.dots{left:560px;top:571px;display:flex;gap:6px}
.dots span{width:18px;height:18px;border-radius:50%;background:var(--paper)}
.dots span.on{background:var(--gold-deep);border:3px solid var(--paper)}

/* about */
.portrait-ring{left:152px;top:680px;width:308px;height:308px;border-radius:50%;border:8px solid #111;background:var(--paper);padding:6px}
.portrait{width:100%;height:100%;border-radius:50%;background:radial-gradient(circle at 45% 40%,#d9b28c,#7a5a3e 55%,#2c2521)}
.about-title{left:484px;top:694px;font-family:"Raleway",sans-serif;font-size:28px;color:#111}
.about-sub{left:484px;top:735px;font-family:"Raleway",sans-serif;font-size:23px;color:#111}
.about-text{left:490px;top:786px;width:570px;font-size:14px;line-height:21px;color:var(--muted)}
.about-text p{margin-bottom:14px}
.about-btn{left:486px;top:930px;width:137px;height:39px;font-size:15px}

/* relax band */
.relax{left:0;top:1054px;width:603px;height:399px;background:var(--gold)}
.relax-title{left:143px;top:1134px;font-family:"Raleway",sans-serif;font-size:28px;color:#222}
.relax-text{left:145px;top:1186px;width:400px;font-size:13px;line-height:22px;color:#6b5515}
.relax-btn{left:145px;top:1334px;width:112px;height:34px;border:2px solid #222;color:#222;font-size:13px;display:flex;align-items:center;justify-content:center}
.relax-photo{left:603px;top:1054px;width:597px;height:399px;background:linear-gradient(160deg,#8c8a86,#b78f5e 45%,#e9e3db 60%,#3a3128)}

/* section headings */
.section-title{width:1200px;left:0;text-align:center;font-family:"Raleway",sans-serif;font-size:25px;font-weight:600;color:#222;letter-spacing:.5px}

/* products */
.products{top:1574px;left:0;width:1200px;display:flex;justify-content:center;gap:65px}
.product{width:175px;text-align:center}
.product-img{height:200px;margin:0 auto 14px;width:70px;background:linear-gradient(90deg,#e6e6e6,#fafafa 50%,#dadada);border-radius:10px 10px 4px 4px}
.product-name{font-family:"Raleway",sans-serif;font-size:16px;color:#333;margin-bottom:8px}
.product-desc{font-size:12px;line-height:17px;color:var(--muted);margin-bottom:10px}
.product-btn{width:105px;height:28px;margin:0 auto;border-radius:14px;font-size:11px;font-weight:600}

/* gallery */
.gallery-band{left:0;top:1948px;width:1200px;height:343px;background:var(--band)}
.gallery-item{top:2053px;width:219px;height:172px;padding:6px 10px}
.gallery-item .frame{width:100%;height:100%;border:3px solid var(--paper)}

/* footer */
.footer{left:0;top:2291px;width:1200px;height:271px;background:var(--ink);color:var(--paper)}
.foot-head{font-family:"Raleway",sans-serif;font-size:19px;font-weight:500}
.foot-list{list-style:none;font-size:14px;line-height:25px;color:#ddd}
.foot-addr{font-size:13px;color:#ccc;line-height:24px}
.foot-addr b{font-weight:600;color:var(--paper)}
.foot-bar{left:0;top:2562px;width:1200px;height:62px;background:var(--foot-bar);color:#aaa;font-size:12px}
.social{right:140px;top:12px;display:flex;gap:8px}
.social span{width:30px;height:30px;border-radius:50%;border:2px solid var(--paper)}
</style>
</head>
<body>

<header>
  <div class="abs brand"><span class="brand-dot"></span><span class="brand-name">Quill Petal Loft</span></div>
  <div class="abs phone">
    <div class="phone-label">Phone Number</div>
    <div class="phone-line">
      <span class="phone-icon"><svg width="16" height="16" viewBox="0 0 24 24"><path fill="#fff" d="M6.6 10.8a15 15 0 0 0 6.6 6.6l2.2-2.2c.3-.3.7-.4 1-.2 1.1.4 2.3.6 3.6.6.6 0 1 .4 1 1V20c0 .6-.4 1-1 1A17 17 0 0 1 3 4c0-.6.4-1 1-1h3.5c.6 0 1 .4 1 1 0 1.3.2 2.5.6 3.6.1.3 0 .7-.2 1z"/></svg></span>
      631.555.0142
    </div>
  </div>
</header>

<nav class="abs nav">
  <ul>
    <li class="active">HOME</li><li>ABOUT</li><li>MENUS</li><li>PRODUCTS</li><li>LOCATION</li><li>PRESS</li><li>BOOK NOW</li>
  </ul>
</nav>

<section>
  <div class="abs hero" role="img" aria-label="Salon interior with curling irons and dryers hanging on a rack"></div>
  <svg class="abs hero-curve" width="1200" height="112" viewBox="0 0 1200 112"><path d="M0 112 L0 110 Q600 -20 1200 110 L1200 112 Z" fill="#fff"/></svg>
  <div class="abs hero-kicker">WE HELP YOU TO</div>
  <div class="abs hero-title">GROW YOUR BEAUTY</div>
  <p class="abs hero-text">QUILL PETAL LOFT offers affordable luxury at its finest. Visit us before or after work, get in and out before dinner</p>
  <div class="abs btn-gold hero-btn">SHOP NOW</div>
  <div class="abs dots"><span class="on"></span><span></span><span></span><span></span></div>
</section>

<section>
  <div class="abs portrait-ring"><div class="portrait" role="img" aria-label="Portrait of the salon founder in the shop"></div></div>
  <h2 class="abs about-title">Quill Petal Loft, Hair Spa in the Hamptons,</h2>
  <h3 class="abs about-sub">Manhasset, and coming soon to Englewood, Nj!</h3>
  <div class="abs about-text">
    <p>Quill Petal Loft are specialized salons designed for blowouts, cuts, keratin treatments, and makeup. The shops feature state of the art facilities, custom servicing anyone who wants to enjoy great looking hair!</p>
    <p>Quill Petal Loft offers affordable luxury at its finest. Visit us before or after work, get in and out before dinner, or stay and hang as long as you want!</p>
  </div>
  <div class="abs btn-gold about-btn">READ MORE</div>
</section>

<section>
  <div class="abs relax"></div>
  <h2 class="abs relax-title">Site Back &amp; Relax</h2>
  <p class="abs relax-text">We all know how glamorous the Hamptons are, but we needed a place for a quick fix where women could take their bed head from flat to fab in less than an hour, without spending a fortune. With all the events that take place in the Hamptons, you have to be camera ready almost every night. Opening Quill Petal Hampton made blowouts more accessible to these women</p>
  <div class="abs relax-btn">Read More</div>
  <div class="abs relax-photo" role="img" aria-label="Three friends with fresh blowouts chatting outdoors"></div>
</section>

<section>
  <h2 class="abs section-title" style="top:1498px">OUR PRODUCTS</h2>
  <div class="abs products">
    <div class="product"><div class="product-img" role="img" aria-label="Shampoo bottle"></div><div class="product-name">Product Name</div><p class="product-desc">Ut nisi erat fermentum vel congue id euismod in elit Fusce ultricie</p><div class="btn-gold product-btn">BUY NOW</div></div>
    <div class="product"><div class="product-img" role="img" aria-label="Conditioner bottle"></div><div class="product-name">Product Name</div><p class="product-desc">Ut nisi erat fermentum vel congue id euismod in elit Fusce ultricie</p><div class="btn-gold product-btn">BUY NOW</div></div>
    <div class="product"><div class="product-img" role="img" aria-label="Spray bottle" style="width:52px"></div><div class="product-name">Product Name</div><p class="product-desc">Ut nisi erat fermentum vel congue id euismod in elit Fusce ultricie</p><div class="btn-gold product-btn">BUY NOW</div></div>
    <div class="product"><div class="product-img" role="img" aria-label="Hairspray can" style="width:40px;border-radius:4px"></div><div class="product-name">Product Name</div><p class="product-desc">Ut nisi erat fermentum vel congue id euismod in elit Fusce ultricie</p><div class="btn-gold product-btn">BUY NOW</div></div>
  </div>
</section>

<section>
  <div class="abs gallery-band"></div>
  <h2 class="abs section-title" style="top:1986px">OUR GALLERY</h2>
  <div class="abs gallery-item" style="left:143px;background:linear-gradient(135deg,#3a2a22,#a77c62 50%,#e6d8cf)" role="img" aria-label="Client with long curled dark hair"><div class="frame"></div></div>
  <div class="abs gallery-item" style="left:373px;background:linear-gradient(135deg,#6b5240,#c9a17c 50%,#8a7d74)" role="img" aria-label="Soft balayage waves"><div class="frame"></div></div>
  <div class="abs gallery-item" style="left:603px;background:linear-gradient(135deg,#cdbfb4,#7a5a44 50%,#efe9e4)" role="img" aria-label="Stylist blow drying long hair"><div class="frame"></div></div>
  <div class="abs gallery-item" style="left:833px;background:linear-gradient(135deg,#2a2220,#6d5547 50%,#c6b3a6)" role="img" aria-label="Hair color being applied at the part"><div class="frame"></div></div>
</section>

<footer>
  <div class="abs footer">
    <div class="abs" style="left:143px;top:52px"><div class="foot-head" style="margin-bottom:12px">Quick Links</div><ul class="foot-list"><li>Home</li><li>About Us</li><li>Menu</li><li>Products</li></ul></div>
    <div class="abs" style="left:334px;top:52px"><div class="foot-head" style="margin-bottom:12px">Resources</div><ul class="foot-list"><li>Locations</li><li>Press</li><li>Book Now</li><li>Contact Us</li></ul></div>
    <div class="abs" style="left:507px;top:52px"><div class="foot-head" style="margin-bottom:14px">Contact Info</div>
      <div class="foot-addr">18 Linden Row, East Hampton, NY<br><b>Phone: 631.555.0142</b></div>
      <div class="foot-addr" style="margin-top:14px">905 Meadow Street, Bridgehampton, NY<br><b>Phone: 631.555.0163</b></div>
    </div>
    <div class="abs" style="left:789px;top:90px">
      <div class="foot-addr">240 Harbor Lane, Manhasset, NY<br><b>Phone: 516.555.0187</b></div>
      <div class="foot-addr" style="margin-top:14px">COMING SOON Englewood, NJ<br><b>Phone: 201.555.0129</b></div>
    </div>
  </div>
  <div class="abs foot-bar">
    <div class="abs" style="left:143px;top:23px">© 2016 Company Name &nbsp;All right reserved &nbsp;Term of Use</div>
    <div class="abs social"><span></span><span></span><span></span><span></span></div>
  </div>
</footer>

</body>
</html>
```